KAJU Freightways #ALLKAJU Business Cards & Letterhead

I am looking to business cards designed for our organization. We are currently undergoing a small re-branding that is taking place. Our organization is called KAJU Freightways and we are headquartered in Phoenix, AZ. We primarily provide transportation and logistics services to the Marlow Parcel Bureau who is our largest customer. I would like to see a design that incorporates name, title, contact info, website, and address (this will be different depending on the employee). I would also like to see some color on the business card using our logo colors or a variation. I would like our logo on the back of the business card with the website displayed. The final design should communicate that we are a next generation transportation operate that focuses on being driver-first, customer-centric, innovative, and sustainable.We would also like our #ALLKAJU catch phrase incorporated as well.

Target Market(s)

Transportation & Logistics

Industry/Entity Type

Trucking Company

Contact Information for Business Card

-First and Last Name
-Position Title
-Contact Phone
-Contact Email
-Physical Address

Font styles to use
Serif

Colors

Designer to choose colors to be used in the design.

Requirements
Must have
• -KAJU logo prominently displayed
• -#ALLKAJU catch phrase used
• -Some amount of color, design gradient, etc.
• -Logo on the back with website listed (https://www.kajufreightco.example)

```html
<!DOCTYPE html>
<html lang="en">
<head>
<meta charset="utf-8">
<title>KAJU Freightways Business Card</title>
<link href="https://fonts.googleapis.com/css2?family=Lato:wght@400;700;900&display=swap" rel="stylesheet">
<style>
  :root {
    --teal: #053a45;
    --green: #7dc242;
    --white: #ffffff;
    --ground: #c9cacb;
  }
  * { margin: 0; padding: 0; box-sizing: border-box; }
  html, body { width: 1200px; height: 802px; overflow: hidden; }
  body { background: var(--ground); font-family: "Lato", sans-serif; position: relative; }
  .card {
    position: absolute; top: 274px; width: 443px; height: 264px; overflow: hidden;
    box-shadow: 0 3px 6px rgba(0,0,0,.35);
  }
  .card-front { left: 136px; background: var(--white); }
  .card-back { left: 624px; background: var(--teal); }
  .front-waves { position: absolute; inset: 0; }
  .brand-mark {
    position: absolute; left: 30px; top: 78px; display: flex; align-items: center; gap: 8px;
    color: var(--teal); font-weight: 900; font-size: 38px; letter-spacing: 1px;
  }
  .brand-dot { width: 14px; height: 14px; border-radius: 50%; background: var(--green); }
  .person { position: absolute; right: 22px; top: 33px; text-align: right; }
  .person-name { color: var(--teal); font-weight: 700; font-size: 15px; letter-spacing: .3px; }
  .person-title { color: var(--green); font-size: 12.5px; margin-top: 1px; }
  .contact { position: absolute; right: 22px; top: 156px; text-align: right; color: var(--white); font-size: 12.5px; line-height: 16px; }
  .contact-line { display: flex; justify-content: flex-end; align-items: center; gap: 2px; }
  .contact-line svg { width: 10px; height: 10px; }
  .company { color: var(--green); margin-top: 7px; }
  .hashtag { position: absolute; left: 48px; top: 226px; color: var(--white); font-size: 12.5px; }
  .back-name {
    position: absolute; left: 0; right: 0; top: 106px; text-align: center;
    color: var(--white); font-weight: 900; font-size: 60px; letter-spacing: 2px;
  }
  .back-web { position: absolute; left: 0; right: 0; top: 221px; text-align: center; color: var(--green); font-size: 12px; }
</style>
</head>
<body>
  <section class="card card-front">
    <svg class="front-waves" viewBox="0 0 443 264" width="443" height="264" aria-hidden="true">
      <path d="M0,188 C60,228 150,232 240,190 S380,118 443,148 L443,264 L0,264Z" fill="var(--teal)"/>
      <path d="M0,160 C70,214 150,214 240,172 S350,118 430,138" fill="none" stroke="var(--green)" stroke-width="6"/>
      <path d="M20,194 C90,222 160,218 245,180 S370,120 443,150" fill="none" stroke="var(--white)" stroke-width="3"/>
    </svg>
    <div class="brand-mark"><span class="brand-dot"></span>KAJU</div>
    <div class="person">
      <div class="person-name">DORIAN PELLWORTH</div>
      <div class="person-title">Managing Director</div>
    </div>
    <div class="contact">
      <div class="contact-line">044-555 010 233
        <svg viewBox="0 0 10 10" aria-hidden="true"><path d="M1,3 Q5,0 9,3 L8,4.5 L6.5,3.8 L6.5,3 Q5,2.5 3.5,3 L3.5,3.8 L2,4.5Z M2,6 L8,6 L8,9 L2,9Z" fill="var(--green)"/></svg>
      </div>
      <div class="contact-line">info@kajumail.example
        <svg viewBox="0 0 10 10" aria-hidden="true"><rect x="1" y="2" width="8" height="6" fill="var(--green)"/><path d="M1,2 L5,5.5 L9,2" fill="none" stroke="var(--teal)" stroke-width=".8"/></svg>
      </div>
      <div class="company">KAJU Freightways</div>
      <div>88, Mesa Row Suite</div>
      <div>Phoenix, 85004, Arizona</div>
    </div>
    <div class="hashtag">#ALLKAJU</div>
  </section>

  <section class="card card-back">
    <div class="back-name">KAJU</div>
    <div class="back-web">www.kajufreightco.example</div>
  </section>
</body>
</html>
```